Poster

I need a poster for my business, www.coastalsupperroutesnerja.example which some information about the most important activities (Sangria Tasting, Iberian Ham, Charcuteries & Sherry Wine Tasting, Sailboat Experiences and Picnic Experiences). A3 Format. Social media included (@coastalsupperroutescsr), contact information included.

```html
<!DOCTYPE html>
<html lang="en">
<head>
<meta charset="utf-8">
<title>Coastal Supper Routes Nerja – Activities Poster</title>
<link rel="stylesheet" href="https://fonts.googleapis.com/css2?family=Marcellus&family=Montserrat:ital,wght@0,500;0,600;1,500&display=swap">
<style>
  :root {
    --stage: #eeeeee;
    --paper: #f6f5f3;
    --orange: #f2a21e;
    --ink: #111111;
    --brand-grey: #4a4a4a;
    --white: #ffffff;
  }
  * { margin: 0; padding: 0; box-sizing: border-box; }
  html, body { width: 1200px; height: 1200px; overflow: hidden; background: var(--stage); }
  .poster {
    position: absolute; left: 252px; top: 103px;
    width: 713px; height: 1007px;
    background: var(--paper); overflow: hidden;
    box-shadow: 0 6px 18px rgba(0,0,0,0.12);
  }
  .photo-collage { position: absolute; left: 0; top: 0; width: 713px; height: 1007px; }

  .brand {
    position: absolute; left: 35px; top: 50px; width: 200px;
    font-family: "Montserrat", sans-serif; font-weight: 600;
    font-size: 22px; line-height: 28px; color: var(--brand-grey);
  }
  .tagline {
    position: absolute; left: 251px; top: 62px;
    font-family: "Marcellus", serif; font-weight: 400; font-size: 40px; line-height: 44px;
    color: var(--ink); white-space: nowrap; letter-spacing: -0.6px;
  }

  .url-band { position: absolute; left: 76px; top: 164px; width: 588px; height: 41px; }
  .url-band svg { position: absolute; inset: 0; width: 100%; height: 100%; }
  .url-band span {
    position: absolute; left: 0; right: 0; top: 0; line-height: 41px; text-align: center;
    font-family: "Montserrat", sans-serif; font-weight: 500; font-size: 25px;
    color: var(--white); letter-spacing: 0.3px;
  }

  .headline {
    position: absolute; left: 64px; top: 234px;
    font-family: "Marcellus", serif; font-weight: 400; font-size: 118px; line-height: 118px;
    color: var(--ink); white-space: nowrap; letter-spacing: -1.5px;
  }

  .activity-list { list-style: none; }
  .activity {
    position: absolute; left: 33px; display: flex; align-items: center; gap: 14px;
    font-family: "Montserrat", sans-serif; font-weight: 500; font-size: 25px;
    line-height: 33px; color: var(--ink); white-space: nowrap;
  }
  .activity svg { width: 36px; height: 36px; flex: none; }
  .activity--two-line svg { align-self: center; }

  .contact {
    position: absolute; left: 45px; top: 729px;
    font-family: "Marcellus", serif; font-size: 43px; line-height: 44px; color: var(--ink);
    border-bottom: 3px solid var(--orange); letter-spacing: -1px; white-space: nowrap;
  }

  .social { position: absolute; left: 282px; top: 914px; width: 414px; height: 41px; }
  .social svg { position: absolute; inset: 0; width: 100%; height: 100%; }
  .social .at {
    position: absolute; left: 0; top: 0; width: 42px; height: 41px; text-align: center;
    font-family: "Montserrat", sans-serif; font-weight: 600; font-size: 26px; line-height: 40px; color: var(--white);
  }
  .social .handle {
    position: absolute; left: 50px; top: 0; line-height: 41px;
    font-family: "Montserrat", sans-serif; font-style: italic; font-weight: 500;
    font-size: 24.5px; color: var(--white); white-space: nowrap;
  }
</style>
</head>
<body>
<main class="poster">
  <svg class="photo-collage" viewBox="0 0 713 1007" role="img" aria-label="Photo collage: sailboat at sunset on the sea, friends tasting sangria, chef cooking paella in a wine shop, sangria on a terrace at dusk, beach picnic, olives and charcuterie, picnic basket with croissants">
    <defs>
      <clipPath id="collage-shape">
        <path d="M713 245 C680 320 610 360 545 385 C495 402 455 425 424 445 L424 452 L409 452 C380 452 359 473 359 502 L359 780 C359 815 330 830 290 830 C250 830 200 808 150 808 C90 808 40 830 0 850 L0 1007 L713 1007 Z"/>
      </clipPath>
      <linearGradient id="sail-sky" x1="0" y1="0" x2="0.6" y2="1">
        <stop offset="0" stop-color="#c9d3dc"/><stop offset="0.35" stop-color="#ecd9b0"/><stop offset="0.6" stop-color="#b7b4a8"/><stop offset="1" stop-color="#4f6f86"/>
      </linearGradient>
      <linearGradient id="tasting" x1="0" y1="0" x2="1" y2="1">
        <stop offset="0" stop-color="#5b504b"/><stop offset="0.45" stop-color="#d8ccc3"/><stop offset="0.8" stop-color="#b9a9b6"/><stop offset="1" stop-color="#7a1f26"/>
      </linearGradient>
      <linearGradient id="chef" x1="0" y1="0" x2="1" y2="1">
        <stop offset="0" stop-color="#2f3a33"/><stop offset="0.4" stop-color="#e6d3b4"/><stop offset="0.65" stop-color="#7fbfc6"/><stop offset="1" stop-color="#3b3632"/>
      </linearGradient>
      <linearGradient id="terrace" x1="0" y1="0" x2="0" y2="1">
        <stop offset="0" stop-color="#4d79a8"/><stop offset="0.35" stop-color="#b9a27c"/><stop offset="0.65" stop-color="#6f6a78"/><stop offset="1" stop-color="#4a2e63"/>
      </linearGradient>
      <linearGradient id="beach" x1="0" y1="0" x2="1" y2="1">
        <stop offset="0" stop-color="#d7d0c4"/><stop offset="0.5" stop-color="#b3aca6"/><stop offset="1" stop-color="#8f9aae"/>
      </linearGradient>
      <linearGradient id="olives" x1="0" y1="0" x2="1" y2="0.4">
        <stop offset="0" stop-color="#5a4a2a"/><stop offset="0.5" stop-color="#2a2420"/><stop offset="1" stop-color="#1d3a33"/>
      </linearGradient>
      <linearGradient id="basket" x1="0" y1="0" x2="1" y2="1">
        <stop offset="0" stop-color="#a9b6c6"/><stop offset="0.5" stop-color="#8a6a4e"/><stop offset="1" stop-color="#9aa7bd"/>
      </linearGradient>
      <linearGradient id="croissant" x1="0" y1="0" x2="1" y2="0">
        <stop offset="0" stop-color="#3b4a6e"/><stop offset="0.6" stop-color="#b8c2d6"/><stop offset="1" stop-color="#c98a4e"/>
      </linearGradient>
    </defs>
    <g clip-path="url(#collage-shape)">
      <rect x="0" y="230" width="713" height="370" fill="url(#sail-sky)"/>
      <path d="M359 502 C359 473 380 452 409 452 L608 452 L608 639 L359 639 Z" fill="url(#tasting)"/>
      <rect x="359" y="639" width="249" height="202" fill="url(#chef)"/>
      <rect x="608" y="588" width="105" height="253" fill="url(#terrace)"/>
      <rect x="0" y="800" width="226" height="207" fill="url(#beach)"/>
      <rect x="226" y="828" width="295" height="179" fill="url(#olives)"/>
      <rect x="521" y="841" width="192" height="166" fill="url(#basket)"/>
      <rect x="315" y="952" width="398" height="55" fill="url(#croissant)"/>
    </g>
  </svg>

  <div class="brand">COASTAL SUPPER<br>ROUTES NERJA</div>
  <h2 class="tagline">TRY OUR EXPERIENCES!!!</h2>

  <div class="url-band">
    <svg viewBox="0 0 588 41" preserveAspectRatio="none" aria-hidden="true"><polygon points="18,0 588,0 570,41 0,41" fill="var(--orange)"/></svg>
    <span>www.coastalsupperroutesnerja.example</span>
  </div>

  <h1 class="headline">ACTIVITIES</h1>

  <ul class="activity-list">
    <li class="activity" style="top:376px">
      <svg viewBox="0 0 38 38" aria-hidden="true"><circle cx="16" cy="22" r="15" fill="var(--orange)"/><rect x="13" y="10" width="19" height="23" rx="3" fill="var(--paper)" stroke="var(--ink)" stroke-width="2"/><circle cx="13" cy="9" r="6" fill="var(--paper)" stroke="var(--ink)" stroke-width="2"/></svg>
      Sangria Tasting
    </li>
    <li class="activity" style="top:443px">
      <svg viewBox="0 0 38 38" aria-hidden="true"><circle cx="15" cy="20" r="15" fill="var(--orange)"/><ellipse cx="23" cy="20" rx="12" ry="8" fill="none" stroke="var(--ink)" stroke-width="2"/><line x1="2" y1="13" x2="18" y2="22" stroke="var(--ink)" stroke-width="2"/><line x1="12" y1="31" x2="36" y2="31" stroke="var(--ink)" stroke-width="2"/></svg>
      Iberian Ham
    </li>
    <li class="activity activity--two-line" style="top:510px">
      <svg viewBox="0 0 38 38" aria-hidden="true"><circle cx="21" cy="24" r="13" fill="var(--orange)"/><path d="M4 2 h12 v8 a6 6 0 0 1 -12 0 z" fill="var(--paper)" stroke="var(--ink)" stroke-width="2"/><line x1="10" y1="16" x2="10" y2="34" stroke="var(--ink)" stroke-width="2"/><line x1="5" y1="34" x2="15" y2="34" stroke="var(--ink)" stroke-width="2"/><polygon points="18,25 34,19 34,31 18,31" fill="var(--orange)" stroke="var(--ink)" stroke-width="2"/></svg>
      <span>Charcuteries &amp;<br>Sherry Wine Tasting</span>
    </li>
    <li class="activity" style="top:610px">
      <svg viewBox="0 0 38 38" aria-hidden="true"><circle cx="19" cy="19" r="16" fill="var(--orange)"/><polygon points="19,2 31,29 7,29" fill="var(--ink)"/><path d="M2 31 h34 l-4 5 h-26 z" fill="var(--paper)" stroke="var(--ink)" stroke-width="2"/></svg>
      Sailboat Experiences
    </li>
    <li class="activity" style="top:677px">
      <svg viewBox="0 0 38 38" aria-hidden="true"><path d="M5 17 a14 14 0 0 1 28 0 z" fill="var(--orange)" stroke="var(--ink)" stroke-width="2"/><rect x="2" y="17" width="34" height="3" fill="var(--ink)"/><path d="M5 20 h28 l-3 15 h-22 z" fill="var(--paper)" stroke="var(--ink)" stroke-width="2"/><line x1="8" y1="26" x2="30" y2="26" stroke="var(--ink)" stroke-width="1.5"/><line x1="9" y1="31" x2="29" y2="31" stroke="var(--ink)" stroke-width="1.5"/></svg>
      Picnic Experiences
    </li>
  </ul>

  <p class="contact">CONTACT US!</p>

  <div class="social">
    <svg viewBox="0 0 414 41" preserveAspectRatio="none" aria-hidden="true"><polygon points="42,0 414,0 392,41 42,41" fill="var(--orange)"/><rect x="0" y="0" width="42" height="41" rx="7" fill="var(--ink)"/></svg>
    <span class="at">@</span>
    <span class="handle">@coastalsupperroutescsr</span>
  </div>
</main>
</body>
</html>
```